Yacht, Boats, Watersports company needs a redesign of business card

Hello Designers!
We are a Boat dealership company that sells fun in the water, we sell boats, Yachts, Kayaks and also yacht WaterSport toys. We are looking to redesign our business cards in to something a little bit more sophisticated. in a way that we can make better use of our company colors. I'm attaching a zipped file containing the company 3 sets of company logo which one is an horizontal another one is a vertical and also a chromed 3d logo. Also is included two set of business cards that we use and also some designs that i think it's interesting. We use PMS 2026c Orange and PMS 7687C Blue. I would like to see at least two different options with the orange as accent and also using blue as an accent color. It's really important for the business cards to have a font option and size that is legible to most people. Our current website is wwww.coralpennant.com. Please visit if you want to have a better feeling of the Boat dealership
You can send Single sided or double side options. We are now using single sided but we may be open for a double side option if we really like the design.
Target Market(s)
Marine, boat sales, yacht sales, water toys sales/
Contact Information for Business Card
Name: Dale Whitcombe
Address: 212 North Fenwick Lane,
Palm Cove, FL 33071
Phone: 555-731-8842
Fax: 954:731-8843
Cell: 555-382-1490
Email: dw@coralpennant.com
Website: coralpennant.com
Requirements
Must have
- the current information of the business card provided.
logo
use the PMS Colors
Nice to have
- a touch of elegance and sophistication but simple
Should not have
- should not have any typography that is hard to read, the card should be simple but yet sophisticated.

```html
<!DOCTYPE html>
<html lang="en">
<head>
<meta charset="utf-8">
<title>Coral Pennant — Business Card</title>
<link rel="stylesheet" href="https://fonts.googleapis.com/css2?family=Arimo:wght@700&family=Source+Sans+3:wght@400;700&display=swap">
<style>
  :root {
    --backdrop: #d1d2d4;
    --frame: #6d6e71;
    --orange: #f27226;
    --blue: #0b57a5;
    --navy: #173f6e;
    --white: #ffffff;
  }
  * { margin: 0; padding: 0; box-sizing: border-box; }
  html, body { width: 1200px; height: 1200px; overflow: hidden; }
  body {
    background: var(--backdrop);
    border: 1px solid var(--frame);
    position: relative;
    font-family: "Source Sans 3", "Myriad Pro", sans-serif;
  }
  .card {
    position: absolute;
    top: 238px;
    width: 419px;
    height: 730px;
    overflow: hidden;
  }
  .card-front { left: 165px; background: var(--white); }
  .card-back { left: 647px; background: var(--blue); }
  .card-shape { position: absolute; inset: 0; width: 100%; height: 100%; }

  .brand {
    position: absolute;
    top: 273px;
    left: 0;
    width: 100%;
    text-align: center;
  }
  .brand-mark {
    display: block;
    width: 62px;
    height: 62px;
    margin: 0 auto 14px;
    border-radius: 50%;
    background: var(--orange);
  }
  .brand-name {
    font-weight: 700;
    font-size: 25px;
    letter-spacing: 4px;
    color: var(--navy);
  }
  .website {
    position: absolute;
    top: 638px;
    left: 0;
    width: 100%;
    display: flex;
    justify-content: center;
    align-items: center;
    gap: 6px;
    color: var(--white);
    font-size: 25px;
  }
  .website svg { width: 15px; height: 15px; }

  .holder-name {
    position: absolute;
    top: 204px;
    left: 0;
    width: 100%;
    text-align: center;
    font-family: "Arimo", Arial, sans-serif;
    font-weight: 700;
    font-size: 32px;
    color: var(--white);
  }
  .contact-list { list-style: none; }
  .contact-item {
    position: absolute;
    left: 0;
    width: 100%;
    color: var(--white);
    font-size: 15px;
    line-height: 20px;
  }
  .contact-icon {
    position: absolute;
    left: 80px;
    width: 26px;
    text-align: center;
  }
  .contact-icon svg { width: 26px; height: 26px; display: block; margin: 0 auto; }
  .contact-text { position: absolute; left: 131px; white-space: nowrap; }
  .item-address { top: 302px; }
  .item-address .contact-icon { top: 2px; }
  .item-phone { top: 381px; }
  .item-phone .contact-icon { top: -6px; }
  .item-fax { top: 452px; }
  .item-cell { top: 521px; }
  .item-cell .contact-icon { top: -8px; }
  .item-cell .contact-icon svg { height: 32px; }
  .item-email { top: 591px; }
  .item-email .contact-icon { top: -4px; }
</style>
</head>
<body>

<section class="card card-front" aria-label="Card front">
  <svg class="card-shape" viewBox="0 0 419 730" preserveAspectRatio="none" aria-hidden="true">
    <polygon points="0,492 210,408 419,492 419,730 0,730" fill="var(--orange)"/>
  </svg>
  <div class="brand">
    <span class="brand-mark" aria-hidden="true"></span>
    <div class="brand-name">CORAL PENNANT</div>
  </div>
  <div class="website">
    <svg viewBox="0 0 24 24" fill="none" stroke="currentColor" stroke-width="1.8" aria-hidden="true">
      <circle cx="12" cy="12" r="10"/><ellipse cx="12" cy="12" rx="4.5" ry="10"/><path d="M2 12h20M4 7h16M4 17h16"/>
    </svg>
    <span>coralpennant.com</span>
  </div>
</section>

<section class="card card-back" aria-label="Card back">
  <svg class="card-shape" viewBox="0 0 419 730" preserveAspectRatio="none" aria-hidden="true">
    <polygon points="0,0 419,0 419,54 210,138 0,54" fill="var(--orange)"/>
  </svg>
  <h1 class="holder-name">Dale Whitcombe</h1>
  <ul class="contact-list">
    <li class="contact-item item-address">
      <span class="contact-icon">
        <svg viewBox="0 0 24 28" fill="none" stroke="currentColor" stroke-width="1.6" aria-hidden="true">
          <path d="M12 26C6 19 3 14.5 3 10.5a9 9 0 0 1 18 0C21 14.5 18 19 12 26z"/><circle cx="12" cy="10" r="2.8"/>
        </svg>
      </span>
      <span class="contact-text">Address: 212 North Fenwick Lane,<br>Palm Cove, FL 33071</span>
    </li>
    <li class="contact-item item-phone">
      <span class="contact-icon">
        <svg viewBox="0 0 26 26" fill="none" stroke="currentColor" stroke-width="1.6" aria-hidden="true">
          <path d="M5 21A11 11 0 1 1 8 23.5L2.5 24.5z"/>
          <path d="M9 8.5c.5-1 1.6-1.3 2.2-.6l1 1.6c.3.6 0 1.2-.5 1.6.7 1.6 2 2.9 3.6 3.6.4-.5 1-.8 1.6-.5l1.6 1c.7.6.4 1.7-.6 2.2-5.4.8-9.6-3.5-8.9-8.9z"/>
        </svg>
      </span>
      <span class="contact-text">555-731-8842</span>
    </li>
    <li class="contact-item item-fax">
      <span class="contact-icon">Fax</span>
      <span class="contact-text">555:731-8843</span>
    </li>
    <li class="contact-item item-cell">
      <span class="contact-icon">
        <svg viewBox="0 0 18 32" fill="none" stroke="currentColor" stroke-width="1.3" aria-hidden="true">
          <rect x="1.5" y="1" width="15" height="30" rx="1.5"/><path d="M1.5 4h15M1.5 27.5h15M7 29.3h4"/>
        </svg>
      </span>
      <span class="contact-text">555-382-1490</span>
    </li>
    <li class="contact-item item-email">
      <span class="contact-icon">
        <svg viewBox="0 0 26 26" fill="none" stroke="currentColor" stroke-width="1.6" aria-hidden="true">
          <circle cx="13" cy="13" r="11.5"/><circle cx="13" cy="13" r="4"/>
          <path d="M17 9v5.5c0 1.8 2.8 2 3-.5a7.8 7.8 0 1 0-3.5 6"/>
        </svg>
      </span>
      <span class="contact-text">dw@coralpennant.com</span>
    </li>
  </ul>
</section>

</body>
</html>
```